Bramblewood Joinery Website

My client Bramblewood Joinery is looking for a redesign for a Word Press Website. Their current site is at www.bramblewoodjoinery.example They are a custom cabinet company, but also create bathroom, living room, bar and entertainment and bedroom cabinets too. They would like a design that emulates the master craftsman work they do yet a contemporary style.

Their current site was designed using Flash elements.

Target Market(s)

Home owners and builders of high end homes

Industry/Entity Type

Entertainment

Font styles to use
Serif
Decorative

Requirements
Must have
• Must show their work and logo using a contemporary style.
Nice to have
• Sliders that showcase their projects.

```html
<!DOCTYPE html>
<html lang="en">
<head>
<meta charset="utf-8">
<title>Bramblewood Joinery</title>
<link href="https://fonts.googleapis.com/css2?family=Open+Sans:ital,wght@0,400;1,400&family=Roboto+Condensed:wght@300;400&display=swap" rel="stylesheet">
<style>
:root{
  --green:#34ac2f;
  --green-line:#5cc457;
  --dark:#1e1e1e;
  --ink:#222;
  --muted:#777;
  --footer-text:#9a9a9a;
  --white:#fff;
}
*{box-sizing:border-box;margin:0;padding:0}
html,body{width:802px;height:1200px;overflow:hidden}
body{position:relative;font-family:'Open Sans',sans-serif;background:var(--green);color:var(--ink)}
.abs{position:absolute}
.hero{left:0;top:0;width:802px;height:442px;background:linear-gradient(160deg,#d9d9d9 0%,#c9c9c9 35%,#eaeaea 60%,#bdbdbd 100%)}
.brand{left:40px;top:24px;width:90px;height:90px;border-radius:50%;background:var(--white);border:3px solid var(--dark);display:flex;align-items:center;justify-content:center;text-align:center;font-family:'Roboto Condensed',sans-serif;font-weight:400;font-size:13px;line-height:1.1;color:var(--dark);padding:8px}
.nav{left:176px;top:65px;width:586px;height:45px;background:var(--white);display:flex;font-family:'Roboto Condensed',sans-serif;font-size:11.5px;color:var(--ink)}
.nav a{display:flex;align-items:center;padding:0 19px;color:inherit;text-decoration:none;white-space:nowrap}
.nav a.active{background:var(--green);color:var(--white);width:71px;justify-content:center;padding:0}
.caption{left:40px;top:175px;width:288px;height:130px;background:rgba(40,40,40,.85);padding:20px 13px}
.caption h1{font-family:'Roboto Condensed',sans-serif;font-weight:300;font-size:27px;line-height:31px;color:var(--white)}
.bars{display:flex;gap:6px;margin-top:19px}
.bars span{width:46px;height:3px;background:var(--white)}
.bars span:first-child{background:var(--green)}
.card{top:352px;width:174px;height:322px;background:var(--white);text-align:center}
.card h2{font-family:'Roboto Condensed',sans-serif;font-weight:300;font-size:22px;line-height:22px;text-align:left;padding:19px 0 0 10px;height:79px;color:var(--ink)}
.card h2 small{display:block;font-size:15px;color:var(--green);line-height:20px}
.card .photo{height:117px}
.card p{font-size:8.5px;line-height:14.5px;color:var(--muted);padding:13px 16px 0}
.btn{display:inline-block;background:var(--green);color:var(--white);font-size:8.5px;border-radius:2px;width:75px;line-height:27px;margin-top:18px}
.rule{left:40px;top:705px;width:722px;height:1px;background:var(--green-line)}
.section-title{font-family:'Roboto Condensed',sans-serif;font-weight:300;font-size:22px;color:var(--white)}
.thumb{top:782px;width:174px;height:127px;border:1px solid #bfe8bd;padding:6px}
.thumb div{width:100%;height:100%}
.footer{left:0;top:952px;width:802px;height:248px;background:var(--dark)}
.footer h3{font-family:'Roboto Condensed',sans-serif;font-weight:300;font-size:22px;color:var(--white)}
.ftext{font-size:8.5px;line-height:15px;color:var(--footer-text)}
.products li{list-style:none;font-size:8.5px;line-height:15px;color:var(--footer-text)}
.products li::before{content:"›";margin-right:8px}
.fbtn{background:var(--green);color:var(--white);font-size:10px;width:74px;height:33px;display:flex;align-items:center;justify-content:center}
.social{width:22px;height:22px;background:#2a2a2a}
</style>
</head>
<body>
<div class="abs hero" role="img" aria-label="Photo of a modern white bathroom with vanity and glass shower"></div>
<div class="abs brand">Bramblewood Joinery</div>
<nav class="abs nav">
  <a class="active">HOME</a><a>WHO WE ARE</a><a>GETTING STARTED</a><a>PROFESSIONAL</a><a>PORTFOLIO</a><a>CONTACT US</a>
</nav>
<div class="abs caption">
  <h1>CLIENT EXPERIENCE<br>IS VERY IMPORTANT FOR US</h1>
  <div class="bars"><span></span><span></span><span></span></div>
</div>

<div class="abs card" style="left:40px">
  <h2>BATHROOM<small>CABINETS</small></h2>
  <div class="photo" role="img" aria-label="Bathroom with dark wood vanity" style="background:linear-gradient(135deg,#8a7868,#4a3a2e)"></div>
  <p>Lorem ipsum dolor sit amet, consectetur adipiscing elit. Sed blandit massa.</p>
  <span class="btn">Read More</span>
</div>
<div class="abs card" style="left:225px">
  <h2>LIVING ROOM<small>CABINETS</small></h2>
  <div class="photo" role="img" aria-label="Living room with media wall cabinets" style="background:linear-gradient(135deg,#6e5f4e,#a8977d)"></div>
  <p>Lorem ipsum dolor sit amet, consectetur adipiscing elit. Sed blandit massa.</p>
  <span class="btn">Read More</span>
</div>
<div class="abs card" style="left:407px">
  <h2>ENTERTAINMENT<small>CABINETS</small></h2>
  <div class="photo" role="img" aria-label="Home bar with shelves of bottles" style="background:linear-gradient(180deg,#2a1a10,#a0602c)"></div>
  <p>Lorem ipsum dolor sit amet, consectetur adipiscing elit. Sed blandit massa.</p>
  <span class="btn">Read More</span>
</div>
<div class="abs card" style="left:589px">
  <h2>BEDROOM<small>CABINETS</small></h2>
  <div class="photo" role="img" aria-label="Bedroom with built-in cabinetry" style="background:linear-gradient(135deg,#9a9288,#4e4a44)"></div>
  <p>Lorem ipsum dolor sit amet, consectetur adipiscing elit. Sed blandit massa.</p>
  <span class="btn">Read More</span>
</div>

<div class="abs rule"></div>
<h2 class="abs section-title" style="left:40px;top:725px">LATEST PROJECTS</h2>
<svg class="abs" style="left:693px;top:726px" width="70" height="32" viewBox="0 0 70 32" aria-hidden="true">
  <g fill="none" stroke="#fff" stroke-width="1.2">
    <circle cx="16" cy="16" r="14.5"/><circle cx="53" cy="16" r="14.5"/>
    <path d="M18 12l-4 4 4 4M51 12l4 4-4 4"/>
  </g>
</svg>
<div class="abs thumb" style="left:40px"><div role="img" aria-label="Dark kitchen island project" style="background:linear-gradient(135deg,#2a2a2a,#6a5a48)"></div></div>
<div class="abs thumb" style="left:224px"><div role="img" aria-label="Cream kitchen with range hood project" style="background:linear-gradient(135deg,#6a5a4a,#d2c8b8)"></div></div>
<div class="abs thumb" style="left:407px"><div role="img" aria-label="Dark cabinet with dishwasher project" style="background:linear-gradient(135deg,#1e1e1e,#8a8a88)"></div></div>
<div class="abs thumb" style="left:589px"><div role="img" aria-label="White drawer bank project" style="background:linear-gradient(135deg,#c8c4bc,#f0eee8)"></div></div>

<footer class="abs footer">
  <h3 class="abs" style="left:40px;top:22px">ABOUT US</h3>
  <p class="abs ftext" style="left:40px;top:66px;width:210px">Aenean nonummy hendrerit mau phasellu porta. Fusce suscipit varius mi sed. Cum sociis natoque penatibus et magnis dis.</p>
  <div class="abs fbtn" style="left:40px;top:135px">Read More</div>

  <h3 class="abs" style="left:318px;top:22px">PRODUCTS</h3>
  <ul class="abs products" style="left:318px;top:66px">
    <li>bathroom cabinets</li><li>living room cabinets</li><li>bar cabinets</li><li>entertainment cabinets</li><li>bedroom cabinets</li>
  </ul>

  <h3 class="abs" style="left:497px;top:22px">TESTIMONIAL</h3>
  <svg class="abs" style="left:714px;top:25px" width="48" height="20" viewBox="0 0 48 20" aria-hidden="true">
    <circle cx="10" cy="10" r="9.5" fill="#666"/><circle cx="37" cy="10" r="9.5" fill="#666"/>
    <path d="M13 10H6M9 6l-4 4 4 4M34 10h7M38 6l4 4-4 4" fill="none" stroke="#1e1e1e" stroke-width="2"/>
  </svg>
  <div class="abs" role="img" aria-label="Portrait of customer service representative" style="left:497px;top:67px;width:67px;height:61px;background:linear-gradient(180deg,#d8c4b0,#f2ebe4)"></div>
  <p class="abs ftext" style="left:576px;top:66px;width:190px">Aenean nonummy hendrerit mau phasellu porta. Fusce suscipit varius mi sed. Cum sociis natoque penatibus et magnis dis.</p>
  <p class="abs" style="left:577px;top:128px;font-size:9.5px;font-style:italic;color:#ddd">Sed ut perspiciatis</p>

  <div class="abs" style="left:40px;top:192px;width:722px;height:1px;background:#3a3a3a"></div>
  <p class="abs" style="left:40px;top:209px;font-size:9.5px;font-style:italic;color:#888">© 2015 bramblewoodjoinery.example. All rights reserved.</p>
  <div class="abs social" style="left:630px;top:206px"></div>
  <div class="abs social" style="left:657px;top:206px"></div>
  <div class="abs social" style="left:684px;top:206px"></div>
  <div class="abs social" style="left:711px;top:206px"></div>
  <div class="abs social" style="left:738px;top:206px"></div>
</footer>
</body>
</html>
```